Multi-Line Insurance PPC Landing Page - Conversion optimized.

We have a PPC landing page used for the general population to get an insurance quote through an agent's site.

We'd like to improve the page for PPC traffic, make it more conversion friendly.

Site should be a single long page.

We will dynamically change the form and headlines on the page depending on what insurance "line" is being called. ie, Lift, Auto, Home, Business.

The enclosed AI file has all of the raw elements we need. We're looking to enhance the design and conversion ability.

Target Market(s)

General public needed insurance services.

Industry/Entity Type

Insurance Broker

Number of Pages Required

1 page

Font styles to use
Sans Serif

Requirements
Must have
• Form, agent picture, name, address.

```html
<!DOCTYPE html>
<html lang="en">
<head>
<meta charset="utf-8">
<title>Insurance Agent – Get An Instant Insurance Quote</title>
<link href="https://fonts.googleapis.com/css2?family=Open+Sans:wght@400;600;700&display=swap" rel="stylesheet">
<style>
:root{
  --blue:#1f5ca8;
  --blue-dark:#174a8c;
  --navy:#0f3566;
  --green:#3d8b1f;
  --green-dark:#2f6f16;
  --grey-bg:#eef0f3;
  --line:#d6dae0;
  --text:#555b63;
  --heading:#2b2f35;
  --white:#ffffff;
}
*{box-sizing:border-box;margin:0;padding:0}
html,body{width:1200px;height:2992px;overflow:hidden}
body{font-family:"Open Sans",Arial,sans-serif;color:var(--text);background:var(--white);font-size:15px;line-height:1.55}

/* Header */
.site-header{height:88px;display:flex;justify-content:space-between;align-items:flex-start;background:var(--white);position:relative}
.brand-tab{background:var(--blue);color:var(--white);font-weight:700;font-size:28px;height:64px;padding:0 60px 0 30px;display:flex;align-items:center;clip-path:polygon(0 0,100% 0,86% 100%,0 100%)}
.header-call{display:flex;align-items:center;gap:12px;padding:14px 40px 0 0}
.call-icon{width:46px;height:46px;border-radius:50%;border:2px solid var(--green);display:flex;align-items:center;justify-content:center}
.call-text small{display:block;font-size:13px;color:var(--text);line-height:1.2}
.call-text strong{font-size:24px;color:var(--heading);line-height:1.2}

/* Hero */
.hero{height:452px;position:relative;background:linear-gradient(100deg,#2b3f5c 0%,#c9a88f 45%,#d9c2ae 60%,#1e2a3a 100%);display:flex;flex-direction:column;align-items:center;justify-content:flex-end;padding-bottom:82px}
.hero-title{color:var(--white);font-size:50px;font-weight:600;text-shadow:0 2px 6px rgba(0,0,0,.35)}
.btn{display:inline-block;color:var(--white);font-weight:700;text-transform:uppercase;border-radius:3px}
.btn-blue{background:var(--blue);font-size:20px;padding:12px 30px;margin-top:10px}
.btn-green{background:var(--green);border-bottom:3px solid var(--green-dark)}

/* Quote section */
.quote-section{height:560px;background:var(--grey-bg);display:flex;gap:40px;padding:70px 80px 0}
.agent-card{width:300px;text-align:center;padding-top:10px}
.agent-photo{width:200px;height:200px;border-radius:50%;margin:0 auto 24px;border:6px solid var(--blue);background:radial-gradient(circle at 50% 40%,#c9b4a2,#27344a 75%)}
.agent-name{font-size:28px;font-weight:600;color:var(--heading)}
.agent-phone{font-size:20px;color:var(--heading);margin:6px 0 16px;display:flex;align-items:center;justify-content:center;gap:8px}
.agent-address{font-size:18px;color:var(--heading);font-weight:600;line-height:1.4}
.quote-form{flex:1;background:var(--white);border:1px solid var(--line);padding:28px 36px}
.quote-form h2{font-size:26px;color:var(--blue);font-weight:600;margin-bottom:22px}
.quote-form h2 span{color:var(--heading)}
.form-grid{display:grid;grid-template-columns:1fr 1fr;column-gap:40px;row-gap:14px}
.field label{display:block;font-size:14px;color:var(--heading);margin-bottom:4px}
.input{height:34px;border:1px solid var(--line);background:#fafbfc;font-size:13px;color:#8a9099;padding:0 10px;display:flex;align-items:center;justify-content:space-between}
.input-row{display:flex;gap:8px}
.input-row .input{flex:1}
.caret{width:0;height:0;border-left:5px solid transparent;border-right:5px solid transparent;border-top:6px solid #8a9099}
.submit{font-size:16px;padding:8px 32px;margin-top:18px}

/* About */
.about{height:160px;text-align:center;padding:22px 120px 0;overflow:hidden}
.section-title{font-size:30px;font-weight:600;color:var(--blue);display:inline-block;border-bottom:2px solid var(--line);padding:0 30px 4px;margin-bottom:10px;line-height:1.4}
.section-title span{color:var(--heading)}
.about p{font-size:14px;line-height:1.5}

/* Products */
.products{height:1052px;background:var(--grey-bg);text-align:center;padding-top:44px}
.product-grid{display:grid;grid-template-columns:repeat(3,300px);column-gap:50px;row-gap:70px;justify-content:center;margin-top:44px}
.product-card{background:var(--white);height:400px;box-shadow:0 2px 6px rgba(0,0,0,.12);position:relative}
.card-head{background:var(--blue);color:var(--white);height:60px;display:flex;align-items:flex-end;justify-content:center;padding-bottom:8px;font-size:21px;font-weight:600;position:relative}
.card-icon{position:absolute;top:-26px;left:50%;transform:translateX(-50%);width:52px;height:52px;border-radius:50%;background:var(--blue);border:3px solid var(--white);display:flex;align-items:center;justify-content:center}
.card-image{height:130px;margin:10px 12px 0}
.card-body{padding:14px 24px 0;font-size:14px;line-height:1.45;color:var(--text)}
.card-btn{font-size:14px;padding:7px 16px;position:absolute;left:50%;transform:translateX(-50%);bottom:20px;white-space:nowrap}
.img-auto{background:linear-gradient(135deg,#6f7781,#2c3038)}
.img-home{background:linear-gradient(135deg,#e6d2c2,#b8574a)}
.img-life{background:linear-gradient(180deg,#9cc3e4,#e9d8b7)}
.img-health{background:linear-gradient(135deg,#f1e8e6,#c83a3a)}
.img-business{background:linear-gradient(180deg,#a9c0d6,#1b2026)}
.img-disability{background:linear-gradient(180deg,#5f92c8,#d9c7a8)}

/* Reviews */
.reviews{height:280px;text-align:center;padding-top:22px}
.review-grid{display:flex;justify-content:center;gap:60px;margin-top:22px}
.review{display:flex;gap:20px;align-items:flex-start;width:500px;text-align:left}
.review-photo{width:110px;height:110px;border-radius:50%;flex-shrink:0;border:4px solid var(--grey-bg)}
.review-photo.male{background:radial-gradient(circle at 50% 40%,#d2b59c,#3b4450 75%)}
.review-photo.female{background:radial-gradient(circle at 50% 40%,#e4c7ae,#5a3d2e 75%)}
.review-box{background:var(--grey-bg);padding:14px 18px 14px 52px;position:relative;font-size:14px;line-height:1.5}
.review-box .mark{position:absolute;left:14px;top:4px;font-size:44px;color:#b9c0c9;font-weight:700;line-height:1}
.review-name{color:var(--blue);font-weight:700;font-size:15px;margin-top:12px;text-align:center}

/* Companies */
.companies{height:220px;text-align:center;border-top:1px solid var(--line);padding-top:26px}
.company-row{display:flex;align-items:center;justify-content:center;gap:50px;margin-top:34px}
.arrow{width:34px;height:34px;background:var(--blue);display:flex;align-items:center;justify-content:center}
.company{font-size:24px;font-weight:700;color:var(--heading);display:flex;align-items:center;gap:8px}
.company .dot{width:14px;height:14px;background:var(--blue)}

/* Footer */
.site-footer{height:180px;background:var(--navy);color:#c7d3e3;display:flex;justify-content:space-between;padding:22px 60px 0;position:relative}
.disclaimer{width:620px}
.disclaimer h3{color:var(--white);font-size:16px;font-weight:600;margin-bottom:6px}
.disclaimer p{font-size:13px;line-height:1.5}
.disclaimer small{display:block;font-size:12px;margin-top:30px;color:#9fb1c8}
.footer-contact{text-align:right;color:var(--white)}
.footer-contact .phone{font-size:20px;font-weight:600;display:flex;align-items:center;gap:8px;justify-content:flex-end}
.footer-contact .addr{font-size:14px;line-height:1.4;margin-top:6px}
.footer-brand{position:absolute;right:60px;bottom:14px;font-size:30px;font-weight:600;color:var(--white)}
</style>
</head>
<body>

<header class="site-header">
  <div class="brand-tab">Insurance Agent</div>
  <div class="header-call">
    <div class="call-icon">
      <svg width="22" height="22" viewBox="0 0 24 24"><path fill="#3d8b1f" d="M6.6 10.8a15 15 0 0 0 6.6 6.6l2.2-2.2c.3-.3.7-.4 1-.2 1.1.4 2.3.6 3.6.6.6 0 1 .4 1 1V20c0 .6-.4 1-1 1A17 17 0 0 1 3 4c0-.6.4-1 1-1h3.5c.6 0 1 .4 1 1 0 1.3.2 2.5.6 3.6.1.3 0 .7-.2 1z"/></svg>
    </div>
    <div class="call-text"><small>Get a quick quote by phone</small><strong>(555) 014-2288</strong></div>
  </div>
</header>

<section class="hero" role="img" aria-label="Two business people shaking hands">
  <h1 class="hero-title">Business Insurance</h1>
  <span class="btn btn-blue">Get a Quote!</span>
</section>

<section class="quote-section">
  <div class="agent-card">
    <div class="agent-photo" role="img" aria-label="Portrait of the insurance agent"></div>
    <div class="agent-name">Mark Ellison - Agent</div>
    <div class="agent-phone">
      <svg width="18" height="18" viewBox="0 0 24 24"><path fill="#1f5ca8" d="M6.6 10.8a15 15 0 0 0 6.6 6.6l2.2-2.2c.3-.3.7-.4 1-.2 1.1.4 2.3.6 3.6.6.6 0 1 .4 1 1V20c0 .6-.4 1-1 1A17 17 0 0 1 3 4c0-.6.4-1 1-1h3.5c.6 0 1 .4 1 1 0 1.3.2 2.5.6 3.6.1.3 0 .7-.2 1z"/></svg>
      (555) 017-4410
    </div>
    <div class="agent-address">1420 Harbor Ave<br>Fairview, CA 90210</div>
  </div>

  <form class="quote-form">
    <h2>Get An Instant <span>Insurance Quote.</span></h2>
    <div class="form-grid">
      <div class="field"><label>Full Name :</label><div class="input"></div></div>
      <div class="field"><label>Height/Weight :</label><div class="input"></div></div>
      <div class="field"><label>Sex :</label><div class="input">Select<i class="caret"></i></div></div>
      <div class="field"><label>Tobacco Use :</label><div class="input">Select<i class="caret"></i></div></div>
      <div class="field"><label>Date of Birth :</label>
        <div class="input-row">
          <div class="input">Month<i class="caret"></i></div>
          <div class="input">Day<i class="caret"></i></div>
          <div class="input">Year<i class="caret"></i></div>
        </div>
      </div>
      <div class="field"><label>Phone :</label><div class="input"></div></div>
      <div class="field"><label>Current Health :</label><div class="input">Select<i class="caret"></i></div></div>
      <div class="field"><label>Email :</label><div class="input"></div></div>
    </div>
    <span class="btn btn-green submit">Submit</span>
  </form>
</section>

<section class="about">
  <h2 class="section-title">About <span>Insurance Agent</span></h2>
  <p>We help families and business owners find the right coverage at a fair price. I compare plans from many trusted carriers and explain every option in plain language, so you can protect your car, home, health or company with confidence. Call today or use the form above for a free quote.</p>
</section>

<section class="products">
  <h2 class="section-title">Our <span>Insurance Products</span></h2>
  <div class="product-grid">
    <article class="product-card">
      <div class="card-head"><span class="card-icon"><svg width="28" height="20" viewBox="0 0 28 20"><path fill="#fff" d="M4 9l3-6h14l3 6h2v7h-3a3 3 0 0 1-6 0h-6a3 3 0 0 1-6 0H2V9zm4-4l-2 4h16l-2-4z"/></svg></span>Auto Insurance</div>
      <div class="card-image img-auto" role="img" aria-label="Car on the road"></div>
      <p class="card-body">Coverage built around you, with clear terms, fair rates and quick help whenever you need to make a claim.</p>
      <span class="btn btn-green card-btn">Get a Quote! ›</span>
    </article>
    <article class="product-card">
      <div class="card-head"><span class="card-icon"><svg width="24" height="22" viewBox="0 0 24 22"><path fill="#fff" d="M12 1l11 10h-3v10h-6v-6h-4v6H4V11H1z"/></svg></span>Home Insurance</div>
      <div class="card-image img-home" role="img" aria-label="Hands holding a small house"></div>
      <p class="card-body">Coverage built around you, with clear terms, fair rates and quick help whenever you need to make a claim.</p>
      <span class="btn btn-green card-btn">Get a Quote! ›</span>
    </article>
    <article class="product-card">
      <div class="card-head"><span class="card-icon"><svg width="24" height="22" viewBox="0 0 24 22"><path fill="#fff" d="M12 21S2 14 2 7.5A5 5 0 0 1 12 5a5 5 0 0 1 10 2.5C22 14 12 21 12 21z"/></svg></span>Life Insurance</div>
      <div class="card-image img-life" role="img" aria-label="Family playing on a beach"></div>
      <p class="card-body">Coverage built around you, with clear terms, fair rates and quick help whenever you need to make a claim.</p>
      <span class="btn btn-green card-btn">Get a Quote! ›</span>
    </article>
    <article class="product-card">
      <div class="card-head"><span class="card-icon"><svg width="22" height="22" viewBox="0 0 22 22"><path fill="#fff" d="M8 1h6v7h7v6h-7v7H8v-7H1V8h7z"/></svg></span>Health Insurance</div>
      <div class="card-image img-health" role="img" aria-label="Heartbeat line and stethoscope"></div>
      <p class="card-body">Coverage built around you, with clear terms, fair rates and quick help whenever you need to make a claim.</p>
      <span class="btn btn-green card-btn">Get a Quote! ›</span>
    </article>
    <article class="product-card">
      <div class="card-head"><span class="card-icon"><svg width="24" height="20" viewBox="0 0 24 20"><path fill="#fff" d="M8 4V2a1 1 0 0 1 1-1h6a1 1 0 0 1 1 1v2h6a1 1 0 0 1 1 1v13a1 1 0 0 1-1 1H2a1 1 0 0 1-1-1V5a1 1 0 0 1 1-1zm2 0h4V3h-4z"/></svg></span>Business Insurance</div>
      <div class="card-image img-business" role="img" aria-label="Business people holding umbrellas"></div>
      <p class="card-body">Coverage built around you, with clear terms, fair rates and quick help whenever you need to make a claim.</p>
      <span class="btn btn-green card-btn">Get a Quote! ›</span>
    </article>
    <article class="product-card">
      <div class="card-head"><span class="card-icon"><svg width="22" height="24" viewBox="0 0 22 24"><circle cx="9" cy="3" r="2.5" fill="#fff"/><path fill="none" stroke="#fff" stroke-width="2.4" d="M9 7v7h7l3 6M6 11a6 6 0 1 0 8 7"/></svg></span>Disability Insurance</div>
      <div class="card-image img-disability" role="img" aria-label="Person in a wheelchair outdoors"></div>
      <p class="card-body">Coverage built around you, with clear terms, fair rates and quick help whenever you need to make a claim.</p>
      <span class="btn btn-green card-btn">Get a Quote! ›</span>
    </article>
  </div>
</section>

<section class="reviews">
  <h2 class="section-title">Our <span>Customer Review</span></h2>
  <div class="review-grid">
    <div class="review">
      <div class="review-photo male" role="img" aria-label="Customer portrait"></div>
      <div>
        <div class="review-box"><span class="mark">“</span>Switching my policy was easy and saved me money. Every question got a quick, friendly answer.</div>
        <div class="review-name">Mr. Paul Hartley</div>
      </div>
    </div>
    <div class="review">
      <div class="review-photo female" role="img" aria-label="Customer portrait"></div>
      <div>
        <div class="review-box"><span class="mark">“</span>Great service from start to finish. I finally understand what my home policy covers.</div>
        <div class="review-name">Miss. Nora Hartley</div>
      </div>
    </div>
  </div>
</section>

<section class="companies">
  <h2 class="section-title">Insurance <span>Company</span></h2>
  <div class="company-row">
    <span class="arrow"><svg width="12" height="16" viewBox="0 0 12 16"><path d="M10 1L3 8l7 7" fill="none" stroke="#fff" stroke-width="3"/></svg></span>
    <span class="company"><i class="dot"></i>Fernwick</span>
    <span class="company">Holtmara</span>
    <span class="company">Quenvale</span>
    <span class="company">Ostrelin</span>
    <span class="company">Pellidar Tech</span>
    <span class="arrow"><svg width="12" height="16" viewBox="0 0 12 16"><path d="M2 1l7 7-7 7" fill="none" stroke="#fff" stroke-width="3"/></svg></span>
  </div>
</section>

<footer class="site-footer">
  <div class="disclaimer">
    <h3>Disclaimer</h3>
    <p>Quotes are estimates and depend on underwriting. Coverage is subject to policy terms, conditions and exclusions. Not available in all states.</p>
    <small>© 2016 Insurance Agent. All Rights reserved.</small>
  </div>
  <div class="footer-contact">
    <div class="phone">
      <svg width="18" height="18" viewBox="0 0 24 24"><path fill="#fff" d="M6.6 10.8a15 15 0 0 0 6.6 6.6l2.2-2.2c.3-.3.7-.4 1-.2 1.1.4 2.3.6 3.6.6.6 0 1 .4 1 1V20c0 .6-.4 1-1 1A17 17 0 0 1 3 4c0-.6.4-1 1-1h3.5c.6 0 1 .4 1 1 0 1.3.2 2.5.6 3.6.1.3 0 .7-.2 1z"/></svg>
      (555) 017-4410
    </div>
    <div class="addr">1420 Harbor Ave<br>Fairview, CA 90210</div>
  </div>
  <div class="footer-brand">Insurance Agent</div>
</footer>

</body>
</html>
```